Vantoq Business Card Project showing the logo and a marbo image on the rear

Design a whacky but professional business card, the logo is for the front and the Marbo image is for the rear. Happy to consider other open source Marbo Images if the designer wants to select one from the web. Vantoq is a competitor to OMB.com.au and Pellory.com.au and is based around every property in Australia

Target Market(s)

Business

Contact Information for Business Card

Name, Title, Email, Web, Phone Number

Font styles to use
Other font styles liked:
• avenir

Requirements
Must have
• Image on Back logo on front
Nice to have
• Happy to consider other images on rear, preftably Colin Marbo. Image supplied I own, we can use open source other Marbo Images

```html
<!DOCTYPE html>
<html lang="en">
<head>
<meta charset="utf-8">
<title>Vantoq Business Card</title>
<link href="https://fonts.googleapis.com/css2?family=Jost:wght@500;700&family=Roboto:wght@400&display=swap" rel="stylesheet">
<style>
  :root {
    --backdrop: #1f1f1f;
    --card: #f1f1f1;
    --ink: #161616;
    --orange: #ef8a0a;
    --art-a: #e2488f;
    --art-b: #f2c230;
    --art-c: #4db3d8;
    --art-d: #8cc63f;
  }
  * { margin: 0; padding: 0; box-sizing: border-box; }
  html, body {
    width: 1200px; height: 1138px; overflow: hidden;
    background: var(--backdrop);
  }
  .stage { position: relative; width: 1200px; height: 1138px; }
  .card {
    position: absolute;
    background: var(--card);
    border-radius: 16px;
    overflow: hidden;
  }
  /* Front */
  .card--front { left: 274px; top: 186px; width: 623px; height: 376px; }
  .brand {
    position: absolute; top: 52px; left: 0; width: 100%;
    display: flex; justify-content: center; align-items: center; gap: 20px;
  }
  .brand__square { width: 64px; height: 64px; background: var(--orange); }
  .brand__name {
    font-family: "Jost", sans-serif; font-weight: 700;
    font-size: 70px; line-height: 1; color: var(--ink);
  }
  .brand__url {
    position: absolute; top: 140px; left: 0; width: 100%;
    text-align: center;
    font-family: "Roboto", sans-serif; font-size: 16px;
    letter-spacing: 12px; color: var(--ink);
  }
  .city-art {
    position: absolute; left: 0; bottom: 0; width: 100%; height: 178px;
    background: linear-gradient(180deg, var(--art-a) 0%, var(--art-b) 45%, var(--art-c) 78%, var(--art-d) 100%);
  }
  /* Back */
  .card--back { left: 276px; top: 608px; width: 618px; height: 374px; }
  .person { position: absolute; left: 78px; top: 88px; }
  .person__name {
    font-family: "Jost", sans-serif; font-weight: 500;
    font-size: 26px; color: var(--orange); line-height: 1.1;
  }
  .person__title {
    font-family: "Roboto", sans-serif; font-size: 16px; color: var(--ink); margin-top: 4px;
  }
  .contacts {
    position: absolute; left: 78px; top: 166px;
    list-style: none; font-family: "Roboto", sans-serif; font-size: 16px; color: var(--ink);
  }
  .contacts li { display: flex; align-items: center; height: 23.5px; }
  .contacts svg { width: 14px; height: 14px; margin-right: 17px; }
  .contacts .accent { color: var(--orange); }
  .address {
    position: absolute; left: 78px; top: 245px;
    font-family: "Roboto", sans-serif; font-size: 16px; line-height: 20px; color: var(--ink);
  }
  .mark { position: absolute; left: 372px; top: 70px; width: 200px; text-align: center; }
  .mark__square { width: 150px; height: 150px; background: var(--orange); margin: 0 auto; }
  .mark__name {
    font-family: "Jost", sans-serif; font-weight: 700;
    font-size: 46px; line-height: 1; color: var(--ink); margin-top: 30px;
  }
</style>
</head>
<body>
<main class="stage">
  <section class="card card--front">
    <div class="brand">
      <div class="brand__square"></div>
      <div class="brand__name">Vantoq</div>
    </div>
    <div class="brand__url">www.vantoq.com</div>
    <div class="city-art" role="img" aria-label="Colourful cartoon city skyline in the Colin Marbo style, with a train running along the bottom"></div>
  </section>

  <section class="card card--back">
    <div class="person">
      <div class="person__name">Owen Pratley</div>
      <div class="person__title">Founder &amp; CEO</div>
    </div>
    <ul class="contacts">
      <li>
        <svg viewBox="0 0 14 14"><circle cx="7" cy="7" r="6" fill="none" stroke="#ef8a0a" stroke-width="1.4"/><path d="M5 4.2l1 1.6-.7.8a4 4 0 0 0 2.1 2.1l.8-.7 1.6 1-.5 1.1c-2.6.1-5.1-2.4-5-5z" fill="#ef8a0a"/></svg>
        (00) 4815 9026
      </li>
      <li>
        <svg viewBox="0 0 14 14"><rect x="0.5" y="2.5" width="13" height="9" fill="#ef8a0a"/><path d="M0.5 2.5l6.5 5 6.5-5" fill="none" stroke="#f1f1f1" stroke-width="1.2"/></svg>
        pratley@vantoq.com
      </li>
      <li>
        <svg viewBox="0 0 14 14"><circle cx="7" cy="7" r="6" fill="none" stroke="#ef8a0a" stroke-width="1.3"/><ellipse cx="7" cy="7" rx="2.6" ry="6" fill="none" stroke="#ef8a0a" stroke-width="1.1"/><path d="M1 7h12M2 4h10M2 10h10" stroke="#ef8a0a" stroke-width="1"/></svg>
        <span>www.<span class="accent">vantoq</span>.com</span>
      </li>
    </ul>
    <div class="address">Level 4, 18 Harbour Lane,<br>Sydney 2000, Australia</div>
    <div class="mark">
      <div class="mark__square"></div>
      <div class="mark__name">Vantoq</div>
    </div>
  </section>
</main>
</body>
</html>
```